Business Cards for new orthopaedic surgery practice

My husband and I are starting our own orthopaedic surgery practice. We are looking for a business card that is uniform, but one will have my name/title and the other will have his. You can just create one design with my name on it for now. But when I choose your design as the winning design I will ask that you add another copy with his name/title.

We are looking for classy, simple, elite all in one. We like dark blues/a little gold/yellow. Something that goes with our logo. We want our logo incorporated. Here is all the info you need:
Business name: RV Bone & Vitality Center
Location: 38517 North Willowmere Ave
Maple Hollow, FL 33418
Phone: 954-218-4063
Fax: 954-582-7341
Email: info@myrvbonecare.example

Names: Lydia Vance, M.D.
Board Certified Hand and Upper Extremity Surgeon

Ebo Dansu, M.D.
Board Certified Hip & Knee Replacement/General Orthopaedic Surgeon

Can decide what you want to put on the back. Maybe a slogan:
Grounded in Healing. Built for You

I am just going to upload our logo. The only thing is if we select you as the winning design, the location, and phone numbers may change. We will need your help to update that once fully solidified.

Industry/Entity Type

Medical

Contact Information for Business Card

Colors
0054AA
0677BA
7BADD7
CADEEF
E8F1F8
0094D4
00A9DD
6FCCEA
C7EBF8
E9F6FB

Requirements
Must have
• class, appeal,
Should not have
• We want to air on the side of masculine if we are looking at masculine vs. feminine feel. But we still want it classy, sophisticated, and something we will love

```html
<!DOCTYPE html>
<html lang="en">
<head>
<meta charset="utf-8">
<title>RV Bone &amp; Vitality Center — Business Card</title>
<link rel="stylesheet" href="https://fonts.googleapis.com/css2?family=Playfair+Display:wght@700&family=Montserrat:wght@400;500&display=swap">
<style>
  :root {
    --stage: #2a2b2e;
    --navy: #1b2a50;
    --navy-deep: #16224a;
    --navy-light: #2b3f6c;
    --gold: #c9a45c;
    --white: #ffffff;
    --serif: "Playfair Display", Georgia, serif;
    --sans: "Montserrat", Arial, sans-serif;
  }
  * { box-sizing: border-box; margin: 0; padding: 0; }
  html, body { width: 1200px; height: 1200px; overflow: hidden; }
  body {
    background: var(--stage);
    display: flex;
    align-items: center;
    justify-content: center;
    gap: 60px;
  }
  .card {
    position: relative;
    width: 420px;
    height: 720px;
    border-radius: 26px;
    background: var(--navy);
    color: var(--white);
    overflow: hidden;
    font-family: var(--sans);
  }
  .practice-mark {
    position: absolute;
    left: 0; right: 0;
    display: flex;
    flex-direction: column;
    align-items: center;
    gap: 16px;
  }
  .practice-mark__dot {
    width: 34px; height: 34px;
    border-radius: 50%;
    border: 2px solid var(--gold);
  }
  .practice-mark__name {
    font-family: var(--serif);
    font-weight: 700;
    font-size: 27px;
    line-height: 1.25;
    letter-spacing: 1.5px;
    text-align: center;
    color: var(--white);
    text-transform: uppercase;
  }
  .card--front .practice-mark { top: 105px; }

  .name-band {
    position: absolute;
    top: 318px; left: 0; right: 0;
    height: 118px;
    background: var(--gold);
    text-align: center;
    padding-top: 22px;
  }
  .name-band__name {
    font-family: var(--serif);
    font-weight: 700;
    font-size: 25px;
    color: var(--navy);
    letter-spacing: 0.5px;
  }
  .name-band__title {
    margin-top: 6px;
    font-size: 15px;
    line-height: 1.25;
    color: var(--white);
  }

  .contact-icons {
    position: absolute;
    top: 478px; left: 0; right: 0;
    display: flex;
    align-items: center;
    justify-content: center;
    gap: 10px;
  }
  .contact-icons__rule { width: 70px; height: 1px; background: var(--gold); }
  .contact-icons__rule:first-child { margin-right: 6px; }
  .contact-icons__rule:last-child { margin-left: 6px; }
  .contact-icon {
    width: 30px; height: 30px;
    border-radius: 50%;
    border: 1.5px solid var(--gold);
    display: flex; align-items: center; justify-content: center;
  }
  .contact-icon svg { width: 16px; height: 16px; }

  .contact-list {
    position: absolute;
    top: 528px; left: 0; right: 0;
    text-align: center;
    font-size: 17px;
    line-height: 30px;
    letter-spacing: 0.3px;
  }
  .contact-divider {
    position: absolute;
    top: 628px; left: 105px; right: 105px;
    height: 1px; background: var(--gold);
  }
  .address {
    position: absolute;
    top: 642px; left: 0; right: 0;
    text-align: center;
    font-size: 16px;
    line-height: 26px;
  }

  .card--back .watermark {
    position: absolute; inset: 0;
    background: radial-gradient(ellipse at 75% 12%, var(--navy-light) 0%, var(--navy) 45%, var(--navy-deep) 100%);
  }
  .card--back .practice-mark { top: 270px; }
  .tagline {
    position: absolute;
    bottom: 80px; left: 0; right: 0;
    text-align: center;
    font-size: 19px;
    font-weight: 500;
    color: var(--gold);
    letter-spacing: 0.5px;
  }
</style>
</head>
<body>
  <section class="card card--front">
    <div class="practice-mark">
      <div class="practice-mark__dot"></div>
      <div class="practice-mark__name">RV Bone &amp;<br>Vitality Center</div>
    </div>

    <div class="name-band">
      <div class="name-band__name">LYDIA VANCE, M.D.</div>
      <div class="name-band__title">Board Certified Hand and Upper<br>Extremity Surgeon</div>
    </div>

    <div class="contact-icons">
      <span class="contact-icons__rule"></span>
      <span class="contact-icon" aria-label="Phone">
        <svg viewBox="0 0 24 24" fill="none" stroke="#c9a45c" stroke-width="2" stroke-linejoin="round"><path d="M5 3h4l2 5-2.5 1.5a11 11 0 0 0 6 6L16 13l5 2v4a2 2 0 0 1-2 2A16 16 0 0 1 3 5a2 2 0 0 1 2-2z"/></svg>
      </span>
      <span class="contact-icon" aria-label="Fax">
        <svg viewBox="0 0 24 24" fill="none" stroke="#c9a45c" stroke-width="2" stroke-linejoin="round"><path d="M7 9V3h10v6"/><rect x="3" y="9" width="18" height="8" rx="2"/><rect x="7" y="14" width="10" height="7"/></svg>
      </span>
      <span class="contact-icon" aria-label="Email">
        <svg viewBox="0 0 24 24" fill="none" stroke="#c9a45c" stroke-width="2" stroke-linejoin="round"><rect x="3" y="5" width="18" height="14" rx="1"/><path d="M3 6l9 7 9-7"/></svg>
      </span>
      <span class="contact-icons__rule"></span>
    </div>

    <div class="contact-list">
      <div>954-218-4063</div>
      <div>954-582-7341</div>
      <div>info@myrvbonecare.example</div>
    </div>
    <div class="contact-divider"></div>
    <div class="address">
      <div>38517 North Willowmere Ave</div>
      <div>Maple Hollow, FL 33418</div>
    </div>
  </section>

  <section class="card card--back">
    <div class="watermark" role="img" aria-label="Faint enlarged practice emblem as background texture"></div>
    <div class="practice-mark">
      <div class="practice-mark__dot"></div>
      <div class="practice-mark__name">RV Bone &amp;<br>Vitality Center</div>
    </div>
    <div class="tagline">Grounded in Healing. Built for You</div>
  </section>
</body>
</html>
```